Logo, Web and Mobile Designs for enterprise social media platform

All the details are in the attached document, please start reading the scope document first which explains what is this project about and the details about the needed deliverables, after that please read the UI_Requirements document which will detail what is expected regarding the coded web version since this is a coded contest, it is very important that you meet the UI requirements or suggest something else but we will need to agree first before working on the coded version

Good Luck

Target Market(s)

Enterprise Social Media

Industry/Entity Type

Media

Coding

Coded - Design and coding required

Number of Pages Required

5+ page

Font styles to use
Sans Serif

Requirements
Must have
• All the must haves are listed in the scope document so please check before you start

```html
<!DOCTYPE html>
<html lang="en">
<head>
<meta charset="utf-8">
<title>Teamora – Company Page</title>
<link href="https://fonts.googleapis.com/css2?family=Roboto:wght@300;400;500&display=swap" rel="stylesheet">
<style>
:root{
  --blue:#0e9ad6;
  --ink:#222;
  --muted:#8a8a8a;
  --line:#e3e3e3;
  --page:#f4f4f4;
  --card:#fff;
  --footer:#2e2e2e;
}
*{box-sizing:border-box;margin:0;padding:0}
html,body{width:682px;height:1200px;overflow:hidden}
body{position:relative;background:var(--page);font-family:'Roboto',Arial,sans-serif;color:var(--ink)}
.abs{position:absolute}
a{color:inherit;text-decoration:none}

/* top bar */
.topbar{left:0;top:0;width:682px;height:33px;background:#fff}
.brand{left:56px;top:9px;font-size:12px;color:#333}
.menu-btn{left:278px;top:7px;width:21px;height:19px;background:#e6e6e6;border:1px solid #ddd}
.search{left:299px;top:7px;width:175px;height:19px;border:1px solid #e2e2e2;background:#fff;font-size:6px;color:#aaa;padding:6px 10px}
.search-btn{left:478px;top:7px;width:26px;height:19px;background:var(--blue)}
.advanced{left:515px;top:12px;font-size:7.5px;color:#333}
.icon{width:12px;height:12px}

/* nav */
.nav{left:0;top:33px;width:682px;height:28px;background:#fff;border-top:1px solid #eee}
.nav a{position:absolute;top:10px;font-size:7px;color:#555}
.nav .active{color:var(--blue)}
.nav .active::after{content:"";position:absolute;left:0;right:0;top:15px;height:2px;background:var(--blue)}

/* hero */
.hero{left:0;top:61px;width:682px;height:221px;background:linear-gradient(90deg,#efe2cf 0%,#e3cdb0 35%,#9a7a62 62%,#5a3328 82%,#3f211c 100%)}
.hero h1{position:absolute;left:54px;top:56px;font-weight:400;font-size:27px;color:#111;letter-spacing:.3px}
.hero h2{position:absolute;left:55px;top:86px;font-weight:400;font-size:18px;color:#111}
.hero p{position:absolute;left:54px;top:122px;font-weight:300;font-size:14.5px;color:#222}
.hero .arrows{left:640px;top:187px}

/* profile strip */
.profile{left:56px;top:282px;width:570px;height:60px;background:#fff;border-bottom:4px solid #ebebeb;border-right:1px solid #e6e6e6}
.logo-box{left:56px;top:265px;width:87px;height:78px;background:#fff;box-shadow:0 0 3px rgba(0,0,0,.2)}
.logo-box span{position:absolute;left:27px;top:23px;width:32px;height:32px;border-radius:50%;background:var(--blue)}
.company{left:156px;top:291px;font-size:13.5px;color:var(--blue)}
.meta{font-size:7px;color:#555}
.followers{left:503px;top:308px;font-size:7px;color:#555}
.follow-btn{left:552px;top:303px;width:44px;height:17px;background:#f0f0f0;border:1px solid #ddd;font-size:7px;color:#555;text-align:center;line-height:15px}

/* cards */
.card{background:var(--card);border:1px solid #e4e4e4;box-shadow:0 1px 1px rgba(0,0,0,.06)}
.about{left:56px;top:358px;width:365px;height:342px}
.photo{position:absolute;left:0;top:0;width:363px;height:130px}
.body-text{font-size:6.3px;line-height:13.5px;color:#888}
.label{font-size:7px;color:#222}
.value{font-size:6.3px;line-height:12px;color:#999}

.events{left:56px;top:718px;width:365px;height:401px}
.card-title{font-size:13px;color:var(--blue);font-weight:400}
.post-head{font-size:6.3px;line-height:13.5px;color:#888}
.post-head b{font-weight:400;color:var(--blue)}
.thumb{width:101px;height:63px}
.post-title{font-size:7.5px;color:#222}
.actions{font-size:6.5px;color:var(--blue)}
.divider{height:1px;background:var(--line)}
.composer{left:12px;top:308px;width:340px;height:47px;background:#eee}
.composer .who{position:absolute;left:9px;top:7px;font-size:7px;color:var(--blue)}
.composer .input{position:absolute;left:9px;top:22px;width:323px;height:16px;background:#fff;border:1px solid #e4e4e4;font-size:6px;color:#aaa;padding:4px 7px}

.side{left:435px;top:358px;width:191px;height:523px}
.side .card-title{position:absolute;left:10px}
.side .rule{position:absolute;left:10px;width:170px;height:1px;background:var(--line)}
.person{width:45px;height:51px}
.brandtile{width:83px;height:41px;border:1px solid #ddd;background:#fff;font-size:11px;color:#333;display:flex;align-items:center;justify-content:center}
.ev-thumb{width:56px;height:51px}
.ev-title{font-size:7px;color:#222}
.ev-text{font-size:6.2px;line-height:11.5px;color:#999}
.more{font-size:7px;color:var(--blue)}

/* footer */
.footer{left:0;top:1138px;width:682px;height:62px;background:var(--footer);color:#ddd;font-size:7.3px;line-height:16px;padding:20px 0 0 56px}
.footer p{width:580px}
</style>
</head>
<body>

<header class="abs topbar">
  <div class="abs brand">Teamora</div>
  <div class="abs menu-btn"><svg width="19" height="17" viewBox="0 0 19 17"><path d="M5 5h9M5 8.5h9M5 12h9" stroke="#333" stroke-width="1.5"/></svg></div>
  <div class="abs search">Search For people,Jobs,Company.....</div>
  <div class="abs search-btn"><svg width="26" height="19" viewBox="0 0 26 19"><circle cx="12" cy="8.5" r="3.6" fill="none" stroke="#fff" stroke-width="1.6"/><path d="M14.6 11.1l3 3" stroke="#fff" stroke-width="1.8"/></svg></div>
  <div class="abs advanced">Advanced</div>
  <svg class="abs icon" style="left:570px;top:11px" viewBox="0 0 12 12"><rect x="0" y="2" width="12" height="8.5" fill="#222"/><path d="M0 2.5l6 4 6-4" stroke="#fff" fill="none"/></svg>
  <svg class="abs icon" style="left:593px;top:10px" viewBox="0 0 12 12"><path d="M1 0v12" stroke="#222" stroke-width="1.5"/><path d="M2 1h9l-2 3 2 3H2z" fill="#222"/></svg>
  <svg class="abs icon" style="left:615px;top:10px" viewBox="0 0 12 12"><circle cx="6" cy="3.5" r="3" fill="#222"/><path d="M1 12c0-4 2-5.5 5-5.5s5 1.5 5 5.5z" fill="#222"/></svg>
</header>

<nav class="abs nav">
  <a class="active" style="left:56px">Home</a>
  <a style="left:93px">Profile</a>
  <a style="left:132px">Connections</a>
  <a style="left:191px">Jobs</a>
  <a style="left:225px">Interests</a>
  <a style="left:520px">Business Services</a>
  <a style="left:598px">Upgrade</a>
</nav>

<section class="abs hero" role="img" aria-label="Banner photo of a microphone on a stand in front of a blurred conference audience">
  <h1>Join the world’s largest</h1>
  <h2>professional network</h2>
  <p>Opportunity is always within reach</p>
  <svg class="abs arrows" width="22" height="14" viewBox="0 0 22 14"><path d="M8 1L2 7l6 6M14 1l6 6-6 6" stroke="#fff" fill="none" stroke-width="1.4"/></svg>
</section>

<section class="abs profile"></section>
<div class="abs logo-box"><span></span></div>
<div class="abs company">Teamora</div>
<div class="abs meta" style="left:156px;top:312px">Design</div>
<div class="abs meta" style="left:156px;top:323px;font-size:6px">1-56 Employees</div>
<div class="abs followers">50 Followers</div>
<div class="abs follow-btn">Follow</div>
<svg class="abs" style="left:603px;top:307px" width="9" height="8" viewBox="0 0 9 8"><path d="M5 0l4 3.5L5 7V5C2.5 5 1 6 0 8 0.4 4.5 2 2.5 5 2z" fill="#555"/></svg>

<!-- About card -->
<section class="abs card about">
  <div class="photo" role="img" aria-label="Photo of business people shaking hands in a bright office" style="background:linear-gradient(90deg,#4a5a6a 0%,#c8cfd6 35%,#e8ecef 55%,#6f7882 75%,#dfe4e8 100%)"></div>
  <p class="abs body-text" style="left:12px;top:137px;width:340px">Sed ut perspiciatis unde omnis iste natus error sit voluptatem accusantium doloremque laudantium, totam rem aperiam, eaque ipsa quae ab illo inventore veritatis et quasi architecto beatae Sed.</p>
  <p class="abs body-text" style="left:12px;top:171px;width:340px">Sed ut perspiciatis unde omnis iste natus error sit voluptatem accusantium doloremque laudantium, totam rem aperiam, eaque ipsa quae ab illo inventore veritatis et quasi architecto beatae vitae dicta sunt explicabo. Nemo enim ipsam voluptatem quia voluptas sit aspernatur aut odit aut fugit.</p>
  <div class="abs label" style="left:12px;top:228px">Specialties</div>
  <div class="abs value" style="left:12px;top:240px">Web Design, UI Design,UX Design,Tech startrups</div>

  <div class="abs label" style="left:12px;top:261px">Website</div>
  <div class="abs value" style="left:12px;top:273px">http://www.teamora.example</div>
  <div class="abs label" style="left:127px;top:261px">Industry</div>
  <div class="abs value" style="left:127px;top:273px">http://www.teamora.example</div>
  <div class="abs label" style="left:240px;top:261px">Type</div>
  <div class="abs value" style="left:240px;top:273px">Privately Held</div>

  <div class="abs label" style="left:12px;top:294px">Headquarters</div>
  <div class="abs value" style="left:12px;top:306px;width:95px">30,Sed ut perspiciatis unde omnis iste natus</div>
  <div class="abs label" style="left:127px;top:294px">Company Size</div>
  <div class="abs value" style="left:127px;top:306px">http://www.teamora.example</div>
  <div class="abs label" style="left:240px;top:294px">Founded</div>
  <div class="abs value" style="left:240px;top:306px">Privately Held</div>
</section>

<!-- Recent events -->
<section class="abs card events">
  <h3 class="abs card-title" style="left:13px;top:10px">Recent Events</h3>
  <div class="abs divider" style="left:0;top:32px;width:363px"></div>

  <p class="abs post-head" style="left:12px;top:42px;width:342px"><b>Teamora</b> unde omnis iste natus error sit voluptatem accusantium doloremque laudantium, totam rem aperiam, <b>http://ghyt.ki/ghjk20</b> inventore veritatis et quasi architecto beatae Sed.</p>
  <div class="abs thumb" style="left:12px;top:75px;background:linear-gradient(135deg,#c9b7a3,#7a6a60 60%,#e6ddd2)" role="img" aria-label="Photo of a speaker presenting to a seated audience"></div>
  <div class="abs post-title" style="left:122px;top:77px">Sed ut perspiciatis unde omnis iste natus error sit voluptatem</div>
  <p class="abs body-text" style="left:122px;top:91px;width:232px">Sed ut perspiciatis unde omnis iste natus error sit voluptatem accusantium doloremque laudantium, totam rem aperiam, eaque ipsa quae ab illo et quasi architecto beatae vitae dicta sunt explicabo.</p>
  <div class="abs actions" style="left:12px;top:146px">Like &nbsp;•&nbsp; Comment &nbsp;•&nbsp; Share &nbsp;•&nbsp; 19 hours ago</div>
  <div class="abs divider" style="left:12px;top:167px;width:340px"></div>

  <p class="abs post-head" style="left:12px;top:182px;width:342px"><b>Teamora</b> unde omnis iste natus error sit voluptatem accusantium doloremque laudantium, totam rem aperiam, <b>http://ghyt.ki/ghjk20</b> inventore veritatis et quasi architecto beatae Sed.</p>
  <div class="abs thumb" style="left:12px;top:215px;background:linear-gradient(135deg,#dfe6ef,#9fb0c6 50%,#f1ece6)" role="img" aria-label="Photo of a woman speaking at a podium microphone"></div>
  <div class="abs post-title" style="left:122px;top:217px">Sed ut perspiciatis unde omnis iste natus error sit voluptatem</div>
  <p class="abs body-text" style="left:122px;top:231px;width:232px">Sed ut perspiciatis unde omnis iste natus error sit voluptatem accusantium doloremque laudantium, totam rem aperiam, eaque ipsa quae ab illo et quasi architecto beatae vitae dicta sunt explicabo.</p>
  <div class="abs actions" style="left:12px;top:286px">Like &nbsp;•&nbsp; Comment &nbsp;•&nbsp; Share &nbsp;•&nbsp; 19 hours ago</div>

  <div class="abs composer">
    <div class="who"><svg width="7" height="7" viewBox="0 0 7 7" style="vertical-align:-1px"><path d="M0 3h1.5v4H0zM2 3l2-3c1 0 1 1 .8 2H7v1.5L6 7H2z" fill="none" stroke="#777" stroke-width=".7"/></svg> Mira Holt</div>
    <div class="input">Post Text / Files</div>
  </div>
  <div class="abs divider" style="left:12px;top:369px;width:340px"></div>
  <svg class="abs" style="left:174px;top:375px" width="14" height="14" viewBox="0 0 14 14"><g fill="#9aa"><circle cx="7" cy="1.5" r="1.2"/><circle cx="11" cy="3" r="1.1" opacity=".8"/><circle cx="12.5" cy="7" r="1" opacity=".7"/><circle cx="11" cy="11" r="1" opacity=".6"/><circle cx="7" cy="12.5" r="1" opacity=".5"/><circle cx="3" cy="11" r="1" opacity=".4"/><circle cx="1.5" cy="7" r="1" opacity=".3"/><circle cx="3" cy="3" r="1.1" opacity=".9"/></g></svg>
</section>

<!-- Sidebar -->
<aside class="abs card side">
  <h3 class="card-title" style="top:9px">People You may Know</h3>
  <div class="rule" style="top:31px"></div>
  <div class="abs person" style="left:10px;top:39px;border:2px solid var(--blue);background:linear-gradient(180deg,#e7edf3,#8aa0bd)" role="img" aria-label="Profile photo of a suggested contact"></div>
  <div class="abs person" style="left:59px;top:39px;background:linear-gradient(180deg,#cbd3dc,#4e5763)" role="img" aria-label="Profile photo of a suggested contact"></div>
  <div class="abs person" style="left:107px;top:39px;background:linear-gradient(180deg,#d9d2cb,#6d6360)" role="img" aria-label="Profile photo of a suggested contact"></div>
  <svg class="abs" style="left:161px;top:57px" width="20" height="12" viewBox="0 0 20 12"><path d="M7 1L2 6l5 5" stroke="#aaa" fill="none" stroke-width="1.5"/><path d="M13 1l5 5-5 5" stroke="var(--blue)" fill="none" stroke-width="1.5"/></svg>
  <div class="abs ev-title" style="left:10px;top:98px">Daniel Rowe</div>
  <div class="abs meta" style="left:10px;top:111px">Design</div>
  <div class="abs meta" style="left:10px;top:122px;font-size:6px">1-56 Employees</div>

  <h3 class="card-title" style="top:150px">People also viewed</h3>
  <div class="rule" style="top:171px"></div>
  <div class="abs brandtile" style="left:10px;top:188px">Halvora</div>
  <div class="abs brandtile" style="left:98px;top:188px">Kestrel</div>
  <div class="abs brandtile" style="left:10px;top:234px">Brenmoor</div>
  <div class="abs brandtile" style="left:98px;top:234px">Lumora</div>

  <h3 class="card-title" style="top:299px">Updated Events</h3>
  <div class="rule" style="top:320px"></div>
  <div class="abs" style="left:178px;top:330px;width:2px;height:48px;background:#ddd"></div>

  <div class="abs ev-thumb" style="left:10px;top:332px;background:linear-gradient(135deg,#b9a797,#5b4c44)" role="img" aria-label="Photo of an audience at a conference"></div>
  <div class="abs ev-title" style="left:82px;top:333px">Sed ut perspiciatis unde &nbsp;iste</div>
  <p class="abs ev-text" style="left:82px;top:346px;width:95px">Sed ut perspiciatis unde omnis iste rem aperiam, eaque</p>
  <div class="abs more" style="left:82px;top:374px">Read More</div>

  <div class="abs ev-thumb" style="left:10px;top:394px;background:linear-gradient(135deg,#d4d8dc,#5f5550)" role="img" aria-label="Photo of a speaker at an event"></div>
  <div class="abs ev-title" style="left:82px;top:395px">Sed ut perspiciatis unde &nbsp;iste</div>
  <p class="abs ev-text" style="left:82px;top:408px;width:95px">Sed ut perspiciatis unde omnis iste rem aperiam, eaque</p>
  <div class="abs more" style="left:82px;top:436px">Read More</div>

  <div class="abs ev-thumb" style="left:10px;top:456px;background:linear-gradient(135deg,#e3e6e9,#6a5b52)" role="img" aria-label="Photo of a woman presenting at a microphone"></div>
  <div class="abs ev-title" style="left:82px;top:457px">Sed ut perspiciatis unde &nbsp;iste</div>
  <p class="abs ev-text" style="left:82px;top:470px;width:95px">Sed ut perspiciatis unde omnis iste rem aperiam, eaque</p>
  <div class="abs more" style="left:82px;top:498px">Read More</div>
</aside>

<footer class="abs footer">
  <p>Help Center | About | Press | Blog | Careers | Mobile | Developers | Teamora Updates | Teamora Influencers | Teamora Jobs | Job Directory | Company Directory | Groups Diectory | User Agreement | Privacy Policy | Cookie Policy | Copyright Policy.</p>
</footer>

</body>
</html>
```